Webdesign für Projektmanagement
Zielgruppe
Projektmanagement und Projektsteuerung von Bauvorhaben für Projektentwickler und Bauträger.
Wesentliche Bereiche sind Wirtschaftliche Steuerung, Steuerung der Baustelle und Bauabläufe sowie Steuerung der Marketing und Vertriebsaktivitäten.
Aufgabenstellung
Orientierung am Logo. Logo und Visitenkarte liegen bei. Schriftart Prelo und Prelo Slab.

```html
<!DOCTYPE html>
<html lang="de">
<head>
<meta charset="utf-8">
<title>Lindgrund Immobilien – Projektmanagement</title>
<link href="https://fonts.googleapis.com/css2?family=Roboto+Slab:wght@400&family=Roboto:wght@400&display=swap" rel="stylesheet">
<style>
  :root {
    --navy: #0c3a52;
    --gold: #b3a064;
    --bg: #f4f4f4;
    --white: #ffffff;
  }
  * { margin: 0; padding: 0; box-sizing: border-box; }
  html, body { width: 1200px; height: 840px; overflow: hidden; }
  body {
    position: relative;
    background: var(--bg);
    color: var(--navy);
    font-family: "Roboto", Arial, sans-serif;
  }
  .hero-visual {
    position: absolute;
    left: 20px; top: 140px;
    width: 1160px; height: 480px;
    background: radial-gradient(ellipse at 50% 55%, #dcdddf 0%, #e8e9ea 40%, rgba(244,244,244,0) 72%);
  }
  .brand {
    position: absolute;
    left: 62px; top: 40px;
    display: flex; align-items: center; gap: 12px;
    font-family: "Roboto Slab", Georgia, serif;
    font-weight: 400;
    font-size: 26px;
    line-height: 1;
    color: var(--navy);
  }
  .brand-square {
    width: 18px; height: 18px;
    background: var(--navy);
  }
  .main-nav {
    position: absolute;
    top: 39px; right: 18px;
    display: flex; gap: 14px;
  }
  .main-nav a {
    display: block;
    padding: 0 8px;
    height: 26px; line-height: 26px;
    font-size: 13px;
    color: var(--navy);
    text-decoration: none;
  }
  .main-nav a.is-active { background: var(--navy); color: var(--white); }
  .hero-text {
    position: absolute;
    left: 0; right: 0; top: 286px;
    text-align: center;
  }
  .hero-title {
    font-family: "Roboto Slab", Georgia, serif;
    font-weight: 400;
    font-size: 47px;
    line-height: 59px;
  }
  .hero-sub { margin-top: 17px; font-size: 15px; }
  .services {
    position: absolute;
    left: 231px; top: 637px;
    display: flex;
  }
  .service {
    width: 185px; height: 148px;
    border-left: 1px solid var(--gold);
    padding: 14px 0 0 12px;
  }
  .service h2 {
    font-family: "Roboto Slab", Georgia, serif;
    font-weight: 400;
    font-size: 22px;
    margin-bottom: 8px;
    white-space: nowrap;
  }
  .service ul { list-style: none; }
  .service li {
    position: relative;
    font-size: 11.5px;
    line-height: 20.3px;
    padding-left: 17px;
  }
  .service li::before {
    content: "";
    position: absolute; left: 4px; top: 8px;
    width: 4px; height: 4px;
    background: var(--navy);
  }
  .site-footer {
    position: absolute;
    left: 0; bottom: 0;
    width: 1200px; height: 26px;
    background: var(--navy);
    color: var(--white);
    font-size: 9px;
    line-height: 26px;
    text-align: center;
  }
</style>
</head>
<body>
  <div class="hero-visual" role="img" aria-label="Blasse Stadtsilhouette mit Hochhäusern und skizzierten Wolken und Pfeilen"></div>

  <div class="brand">
    <span class="brand-square"></span>
    <span class="brand-name">Lindgrund Immobilien</span>
  </div>

  <nav class="main-nav">
    <a href="#" class="is-active">Startseite</a>
    <a href="#">Leistungen</a>
    <a href="#">Über uns</a>
    <a href="#">Referenzen</a>
    <a href="#">Kontakt</a>
  </nav>

  <section class="hero-text">
    <h1 class="hero-title">Projektmanagement<br>und Projektsteuerung</h1>
    <p class="hero-sub">von Bauvorhaben für Projektentwickler und Bauträger</p>
  </section>

  <section class="services">
    <div class="service">
      <h2>Beratung</h2>
      <ul><li>Bestandsaufnahme</li><li>Konzeptentwicklung</li><li>Umsetzungsplanung</li></ul>
    </div>
    <div class="service">
      <h2>Vermarktung</h2>
      <ul><li>Wohnhäuser</li><li>Aufteilungen</li><li>Mehrfamilienhäuser</li><li>Gewerbeimmobilien</li></ul>
    </div>
    <div class="service">
      <h2>Sanierung</h2>
      <ul><li>Gebaudepbnung</li><li>Entkernung</li><li>Ausbau</li><li>Innenraumgestaltung</li></ul>
    </div>
    <div class="service">
      <h2>Bewirtschaftung</h2>
      <ul><li>Objektsteuerung</li><li>Verwaltung</li></ul>
    </div>
  </section>

  <footer class="site-footer">© 2017 Lindgrund Immobilien GmbH</footer>
</body>
</html>
```